Business Card Design Project

I need a business card designed that is clean, simple and elegant.
I am a fashion and advertising photographer based in Cape Town and Durban South Africa.
check out my website: www.marekvollan.co.za for ideas
Updates
Hi all,
Thanks for your submissions so far!
Please note:
I want no more than than black, white and/or grey to be used.
I don't want any photos used.
I would like the card to be double sided.
I would like to continue the design similar to the past ones Ive used.
I hope this helps, please send me further questions should you have any.
many thanks!
Marek
Hi,
Please have a look at the jpg I loaded(called inspiration) which is the direction or inspiration I am aiming at.
Also PLEASE remember NO PHOTOS to be included on the card
many thanks!!
Target Market(s)
You can look at my site to get a better understanding of the audience:
www.marekvollan.co.za
Industry/Entity Type
Advertising
Requirements
Must have
- Clean design which can also be used for a watermark on photographs
perhaps black background with white text/grey
company called: Marek Vollan Photography
Nice to have
- below I have added logos that I have used in the past.
Should not have
- pictures of cameras
tacky elements

```html
<!DOCTYPE html>
<html lang="en">
<head>
<meta charset="utf-8">
<title>Marek Vollan Photography – Business Card</title>
<link rel="stylesheet" href="https://fonts.googleapis.com/css2?family=Jura:wght@500&display=swap">
<style>
  :root {
    --paper: #ffffff;
    --veil: rgba(0, 0, 0, 0.235);
    --ink: #000000;
    --type-light: #ffffff;
  }
  html, body {
    margin: 0;
    padding: 0;
    overflow: hidden;
    background: var(--paper);
  }
  .card {
    position: relative;
    width: 1200px;
    height: 667px;
    overflow: hidden;
    background: var(--paper);
    font-family: "Jura", "Arial", sans-serif;
    font-weight: 500;
  }
  .card__layers {
    position: absolute;
    inset: 0;
  }
  .card__layers rect {
    fill: var(--veil);
  }
  .name-plate {
    position: absolute;
    left: 790px;
    top: 104px;
    width: 410px;
    height: 104px;
    background: var(--ink);
    color: var(--type-light);
    font-size: 33px;
    line-height: 104px;
    padding-left: 37px;
    box-sizing: border-box;
    margin: 0;
    font-weight: 500;
    letter-spacing: 0.3px;
  }
  .contact {
    position: absolute;
    right: calc(1200px - 643px);
    top: 305px;
    margin: 0;
    text-align: right;
    color: var(--type-light);
    font-size: 33px;
    line-height: 54.5px;
    font-style: normal;
    letter-spacing: 0.2px;
  }
  .contact span {
    display: block;
  }
</style>
</head>
<body>
  <main class="card">
    <svg class="card__layers" width="1200" height="667" viewBox="0 0 1200 667" aria-hidden="true">
      <rect class="layer layer--back" x="0" y="0" width="1115" height="667"/>
      <rect class="layer layer--middle" x="77" y="53" width="1095" height="614"/>
      <rect class="layer layer--band" x="0" y="265" width="1200" height="295"/>
    </svg>

    <h1 class="name-plate">Marek Vollan</h1>

    <address class="contact">
      <span class="contact__mobile">+27 (0)82 555 0147</span>
      <span class="contact__office">+27 (0)31 555 0263</span>
      <span class="contact__email">marek@marekvollan.co.za</span>
      <span class="contact__web">www.marekvollan.co.za</span>
    </address>
  </main>
</body>
</html>
```